Stylish High End Wedding Videography/Films Website (BMRT)

We need a modern and high-end website look for our wedding video and films business. We films weddings all over the United Kingdom and at European destinations so need something to reflect our work. The website should be visually stunning with images and videos being the focal point as this is what our services are;

I have uploads of some items I like and the features the site needs to have. These have been taken from other websites using standout features.

We need the following pages;

1 - Homepage
2 - Films Index Page
3 - Individual Films Page
4 - Prices / Collection Page
5 - Reviews
6 - Options
7 - About
8 - Contact
9 - Blog Index
10 - Blog Page

All pages must be consistent so have a similar style.

Pages on menu:
Films
Prices
Reviews
Options
About
Contact

We require a responsive look too. Over 90% of our visitors access the website via their mobile devices.

Please use the colours from our logo to incorporate into the website.

Target Market(s)

Wedding Couples

Industry/Entity Type

Wedding Photography

Number of Pages Required

5+ page

Font styles to use
Sans Serif
Script

Requirements
Must have
• The logo must be in the centre of the menu at the top.

Social icons at the bottom of the page.

Use only two fonts including Lore which is supplied
Nice to have
• Different video for each page on the top header. This will play behind the menu.

```html
<!DOCTYPE html>
<html lang="en">
<head>
<meta charset="utf-8">
<title>BMRT Wedding Films</title>
<link rel="stylesheet" href="https://fonts.googleapis.com/css2?family=Jost:ital,wght@0,300;0,400;0,500;1,300&display=swap">
<style>
:root{
  --ink:#2f2f2f;
  --muted:#555;
  --gold:#a8935c;
  --white:#fff;
  --line:#cfcfcf;
  --badge:#f4e61c;
}
*{margin:0;padding:0;box-sizing:border-box}
html,body{width:1200px;height:4161px;overflow:hidden;background:var(--white)}
body{font-family:"Jost",sans-serif;color:var(--ink);position:relative}
section,header,footer{position:absolute;left:0;width:1200px}
.abs{position:absolute}

/* hero */
.hero{top:0;height:627px;background:
  radial-gradient(ellipse 150px 230px at 700px 470px,rgba(250,248,246,.95),rgba(250,248,246,0) 100%),
  radial-gradient(ellipse 70px 110px at 745px 300px,rgba(60,50,45,.55),rgba(60,50,45,0) 100%),
  linear-gradient(168deg,rgba(0,0,0,0) 55%,rgba(150,120,90,.45) 56%,rgba(222,205,185,.9) 75%),
  linear-gradient(180deg,#eef1f5 0%,#dfe5ea 30%,#9aa4a6 40%,#55646a 55%,#7b6e62 68%,#c9b49c 85%,#e2d5c5 100%)}
.hero__nav{position:absolute;top:107px;left:0;width:1200px;font-size:12px;letter-spacing:1px;color:var(--ink)}
.hero__nav a{position:absolute;color:inherit;text-decoration:none}
.hero__nav .active{border-bottom:2px solid var(--gold);padding-bottom:6px}
.brand{position:absolute;text-align:center;color:var(--ink)}
.brand__mark{display:block;width:40px;height:40px;margin:0 auto 8px;border:2px solid var(--gold)}
.brand__name{font-size:22px;font-weight:500;letter-spacing:5px;display:block}
.brand__sub{font-size:10px;letter-spacing:5px;display:block;margin-top:4px}
.hero__title{position:absolute;left:170px;top:240px;font-size:36px;font-weight:500;letter-spacing:4.5px;line-height:43px;color:var(--ink);white-space:nowrap}

/* intro */
.intro{top:627px;height:523px}
.intro__mark{position:absolute;left:175px;top:48px;width:423px;height:362px;display:flex;align-items:center;justify-content:center;font-size:110px;font-weight:500;letter-spacing:8px;color:var(--ink)}
.intro__text{position:absolute;left:623px;top:100px;font-size:18px;line-height:37.5px;font-weight:300;letter-spacing:.4px;text-transform:uppercase;white-space:nowrap}

/* gallery */
.gallery{top:1150px;height:707px;display:grid;grid-template-columns:repeat(3,400px);grid-template-rows:repeat(3,235.6px)}
.gallery div{width:100%;height:100%}

/* about */
.about{top:1857px;height:490px}
.about__title{position:absolute;left:173px;top:80px;font-size:41px;font-weight:500;line-height:49px;letter-spacing:1px}
.about__text{position:absolute;left:173px;top:190px;font-size:12.5px;line-height:21.5px;color:var(--muted);font-weight:300;white-space:nowrap}
.about__text p+p{margin-top:21px}
.about__photo{position:absolute;left:654px;top:86px;width:428px;height:320px;background:
  radial-gradient(ellipse 110px 150px at 210px 180px,rgba(150,110,90,.55),rgba(150,110,90,0) 100%),
  linear-gradient(90deg,#f4f4f4 0%,#d9d9d9 30%,#7a7a7a 50%,#2a2a2a 72%,#161616 100%)}

/* reviews */
.reviews{top:2347px;height:512px;color:var(--white);background:
  radial-gradient(ellipse 120px 230px at 700px 300px,rgba(245,240,235,.85),rgba(245,240,235,0) 100%),
  radial-gradient(ellipse 110px 250px at 890px 300px,rgba(25,25,30,.8),rgba(25,25,30,0) 100%),
  linear-gradient(180deg,rgba(40,35,30,.55) 0%,rgba(0,0,0,0) 25%),
  linear-gradient(90deg,#33422a 0%,#4a5936 40%,#5a6840 70%,#39432c 100%)}
.reviews__title{position:absolute;left:126px;top:82px;font-size:38px;font-weight:500;letter-spacing:1px}
.reviews__quote{position:absolute;left:170px;top:148px;font-size:17px;line-height:26px;font-style:italic;font-weight:300;white-space:nowrap}
.reviews__mark{position:absolute;font-size:40px;font-weight:500;line-height:1}
.reviews__thanks{position:absolute;left:170px;top:338px;font-size:16px;font-style:italic;font-weight:300}
.reviews__who{position:absolute;left:171px;top:384px;font-size:18px;line-height:26px;font-weight:500;letter-spacing:.5px}

/* videos */
.videos{top:2859px;height:771px}
.videos__title{position:absolute;left:0;width:1200px;top:75px;text-align:center;font-size:41px;font-weight:500;letter-spacing:1px}
.videos__frame{position:absolute;left:173px;top:142px;width:854px;height:434px;background:
  radial-gradient(ellipse 150px 140px at 200px 260px,rgba(235,190,195,.75),rgba(235,190,195,0) 100%),
  radial-gradient(ellipse 90px 200px at 420px 260px,rgba(240,225,215,.55),rgba(240,225,215,0) 100%),
  radial-gradient(ellipse 140px 160px at 740px 230px,rgba(225,205,190,.6),rgba(225,205,190,0) 100%),
  linear-gradient(180deg,rgba(60,40,30,.5) 0%,rgba(0,0,0,0) 30%),
  linear-gradient(90deg,#6e4c55 0%,#84606a 30%,#3a2c30 52%,#4d3c42 75%,#7a6660 100%)}
.videos__text{position:absolute;left:0;width:1200px;top:613px;text-align:center;font-size:12.5px;line-height:21.5px;color:var(--muted);font-weight:300}

/* social strip */
.strip{top:3630px;height:219px;display:grid;grid-template-columns:repeat(6,200px)}
.strip__tile{height:219px}
.strip__btn{position:absolute;left:518px;top:90px;width:162px;height:38px;background:var(--white);display:flex;align-items:center;justify-content:center;gap:8px;font-size:16px;font-weight:500}
.strip__btn i{width:16px;height:16px;border:2px solid var(--ink);border-radius:50%}

/* footer */
.footer{top:3849px;height:312px}
.footer .brand{left:173px;top:60px;width:215px}
.footer .brand__name{font-size:19px;letter-spacing:5px}
.footer .brand__sub{font-size:9px}
.footer h4{position:absolute;top:64px;font-size:15px;font-weight:500;letter-spacing:.5px}
.footer ul{list-style:none;position:absolute;font-size:13px;line-height:22px;color:var(--muted)}
.contact-row{position:absolute;display:flex;align-items:center;gap:10px;font-size:13px;color:var(--ink)}
.contact-row i{width:24px;height:24px;border-radius:50%;background:#2b2b2b;display:flex;align-items:center;justify-content:center}
.contact-row a{color:inherit;text-decoration:underline}
.footer__rule{position:absolute;left:173px;top:232px;width:854px;height:1px;background:var(--line)}
.footer__copy{position:absolute;left:173px;top:262px;font-size:14px}
.footer__badge{position:absolute;left:806px;top:250px;width:222px;height:46px;background:var(--badge);transform:skewX(-10deg)}
</style>
</head>
<body>

<header class="hero" role="img" aria-label="Bride and groom walking arm in arm along a sandy beach at sunset">
  <nav class="hero__nav">
    <a class="active" style="left:172px">HOME</a>
    <a style="left:249px">FILMS</a>
    <a style="left:321px">PRICES</a>
    <a style="left:401px">REVIEWS</a>
    <a style="left:733px">OPTIONS</a>
    <a style="left:827px">ABOUT</a>
    <a style="left:906px">CONTACT</a>
  </nav>
  <div class="brand" style="left:480px;top:40px;width:240px">
    <span class="brand__mark"></span>
    <span class="brand__name">BMRT</span>
    <span class="brand__sub">WEDDING FILMS</span>
  </div>
  <h1 class="hero__title">WEDDING VIDEOGRAPHY<br>NORTH EAST, UK AND<br>WORLDWIDE FILMS</h1>
</header>

<section class="intro">
  <div class="intro__mark">BMRT</div>
  <p class="intro__text">Rowan Tallis is a wedding filmmaker<br>based in the North East of England.<br>We film weddings in a fun and natural<br>way. All weddings are totally unique<br>to the couple. If you are looking for<br>a wedding film for your special day<br>wed love to hear from you.</p>
</section>

<section class="gallery">
  <div role="img" aria-label="Couple kissing beside a stone church tower" style="background:radial-gradient(ellipse 90px 100px at 150px 140px,rgba(25,25,25,.8),rgba(25,25,25,0)),radial-gradient(ellipse 70px 120px at 230px 70px,rgba(200,185,160,.9),rgba(200,185,160,0)),linear-gradient(135deg,#cfd0cc,#6e6e60 60%,#2f3428)"></div>
  <div role="img" aria-label="Couple silhouetted against the sea" style="background:radial-gradient(ellipse 90px 130px at 270px 150px,rgba(25,28,35,.85),rgba(25,28,35,0)),linear-gradient(180deg,#b8b8ac 0%,#9a9a8c 45%,#3e4c52 60%,#56656c 100%)"></div>
  <div role="img" aria-label="Couple holding hands in an autumn garden" style="background:radial-gradient(ellipse 60px 110px at 180px 120px,rgba(30,30,35,.8),rgba(30,30,35,0)),radial-gradient(ellipse 70px 110px at 280px 140px,rgba(240,238,235,.9),rgba(240,238,235,0)),linear-gradient(180deg,#b4512a 0%,#9a5a30 40%,#6f7d4c 75%,#c9c0c8 100%)"></div>
  <div role="img" aria-label="Groom and guest laughing outdoors" style="background:radial-gradient(ellipse 60px 110px at 160px 150px,rgba(170,170,170,.85),rgba(170,170,170,0)),radial-gradient(ellipse 60px 100px at 320px 150px,rgba(30,30,30,.8),rgba(30,30,30,0)),linear-gradient(135deg,#c96a7a,#5c6e44 40%,#4a4e48)"></div>
  <div role="img" aria-label="Bride and groom celebrating indoors" style="background:radial-gradient(ellipse 90px 120px at 110px 160px,rgba(245,240,235,.9),rgba(245,240,235,0)),radial-gradient(ellipse 70px 110px at 260px 160px,rgba(40,40,70,.85),rgba(40,40,70,0)),linear-gradient(135deg,#8a5a36,#c9a27a 60%,#e6d6bf)"></div>
  <div role="img" aria-label="Groom touching bride's face" style="background:radial-gradient(ellipse 80px 130px at 80px 150px,rgba(20,20,22,.9),rgba(20,20,22,0)),radial-gradient(ellipse 90px 110px at 210px 150px,rgba(210,190,170,.7),rgba(210,190,170,0)),linear-gradient(90deg,#403a32,#c8b48e 50%,#e2d2b0)"></div>
  <div role="img" aria-label="Couple kissing among bridesmaids" style="background:radial-gradient(ellipse 70px 110px at 200px 140px,rgba(30,30,30,.8),rgba(30,30,30,0)),radial-gradient(ellipse 60px 110px at 70px 160px,rgba(210,170,190,.8),rgba(210,170,190,0)),radial-gradient(ellipse 70px 110px at 330px 160px,rgba(170,150,175,.8),rgba(170,150,175,0)),linear-gradient(180deg,#c7c2b8,#7a7060)"></div>
  <div role="img" aria-label="Couple walking through autumn flowers" style="background:radial-gradient(ellipse 60px 110px at 180px 120px,rgba(35,35,45,.8),rgba(35,35,45,0)),radial-gradient(ellipse 60px 110px at 280px 150px,rgba(240,238,235,.9),rgba(240,238,235,0)),linear-gradient(180deg,#c25a28 0%,#a8552c 35%,#6c7c48 70%,#d8d2dc 100%)"></div>
  <div role="img" aria-label="Confetti thrown over newlyweds" style="background:radial-gradient(ellipse 60px 100px at 160px 160px,rgba(220,190,180,.8),rgba(220,190,180,0)),radial-gradient(ellipse 70px 110px at 240px 160px,rgba(70,50,70,.9),rgba(70,50,70,0)),radial-gradient(ellipse 60px 90px at 360px 150px,rgba(220,205,200,.8),rgba(220,205,200,0)),linear-gradient(90deg,#342a2e,#6a4e56 60%,#b09a94)"></div>
</section>

<section class="about">
  <h2 class="about__title">ABOUT<br>ROWAN TALLIS</h2>
  <div class="about__text">
    <p>I'm a filmmaker who loves documenting couples' most<br>important day of their lives. Based in County Durham I film<br>weddings mostly in the North East of England however<br>regularly travel around the UK and Europe.</p>
    <p>I first picked up a video camera when I was 8 years old making<br>home movies documenting family holidays and events and it<br>led me onto gaining a degree in TV and Radio Production at<br>University. After University I set up the very first Community<br>Interest Company (CIC) in the UK.</p>
  </div>
  <div class="about__photo" role="img" aria-label="Black and white portrait of the filmmaker"></div>
</section>

<section class="reviews" role="img" aria-label="Bride and groom smiling at each other on a lawn">
  <h2 class="reviews__title">REVIEWS</h2>
  <span class="reviews__mark" style="left:132px;top:150px">"</span>
  <p class="reviews__quote">One of the best decisions We made was<br>choosing you guys to film our wedding! It's<br>absolutely fantastic, it has everyone so<br>emotional watching it, we can't thank you<br>enough for capturing our special day! You<br>were amazing from start to finish <b style="font-style:normal;font-size:30px;vertical-align:-8px">"</b></p>
  <p class="reviews__thanks">Thanks so much.</p>
  <p class="reviews__who">KERRY AND DANIEL<br>THE OLD MILL HOUSE</p>
</section>

<section class="videos">
  <h2 class="videos__title">OUR VIDEOS</h2>
  <svg class="abs" style="left:96px;top:330px" width="30" height="56" viewBox="0 0 30 56"><polyline points="28,2 2,28 28,54" fill="none" stroke="#555" stroke-width="2"/></svg>
  <div class="videos__frame" role="img" aria-label="Video still of confetti thrown over a bride and groom with bridesmaids">
    <svg class="abs" style="left:387px;top:177px" width="80" height="80" viewBox="0 0 80 80"><circle cx="40" cy="40" r="37" fill="none" stroke="#fff" stroke-width="3"/><polygon points="31,24 58,40 31,56" fill="#fff"/></svg>
  </div>
  <svg class="abs" style="left:1068px;top:330px" width="30" height="56" viewBox="0 0 30 56"><polyline points="2,2 28,28 2,54" fill="none" stroke="#555" stroke-width="2"/></svg>
  <p class="videos__text">I have filmed shot some amazing weddings over the years. My main aim is to ensure that<br>couples enjoy their day and that they take in the moments so they remember them. Our<br>wedding films are almost secondary. Here are some amazing words from brides, grooms<br>and couples who we've been so lucky to share their big day with.</p>
</section>

<section class="strip">
  <div class="strip__tile" role="img" aria-label="Bride in lace gown" style="background:radial-gradient(ellipse 60px 110px at 100px 130px,rgba(240,235,230,.9),rgba(240,235,230,0)),linear-gradient(90deg,#5a4038,#9a7a68 50%,#4a3a34)"></div>
  <div class="strip__tile" role="img" aria-label="Coastal ruins under blue sky" style="background:linear-gradient(180deg,#3f72b0 0%,#7aa2cc 40%,#8a7a60 60%,#d6c09a 100%)"></div>
  <div class="strip__tile" role="img" aria-label="Couple among trees" style="background:radial-gradient(ellipse 50px 80px at 110px 160px,rgba(235,235,235,.8),rgba(235,235,235,0)),linear-gradient(180deg,#8a9aa0,#4a5a48 50%,#222)"></div>
  <div class="strip__tile" role="img" aria-label="Couple embracing close up" style="background:radial-gradient(ellipse 70px 80px at 90px 90px,rgba(215,185,160,.85),rgba(215,185,160,0)),linear-gradient(135deg,#d8ccc0,#8a7a68 60%,#6a7a58)"></div>
  <div class="strip__tile" role="img" aria-label="Bride laughing" style="background:radial-gradient(ellipse 70px 90px at 100px 100px,rgba(235,190,160,.9),rgba(235,190,160,0)),linear-gradient(135deg,#a8583c,#d89a74 50%,#e6cfbb)"></div>
  <div class="strip__tile" role="img" aria-label="Newlyweds under confetti" style="background:radial-gradient(ellipse 50px 90px at 80px 150px,rgba(70,50,70,.9),rgba(70,50,70,0)),radial-gradient(ellipse 60px 80px at 160px 120px,rgba(220,200,190,.8),rgba(220,200,190,0)),linear-gradient(90deg,#342a2e,#7a5e62)"></div>
  <div class="strip__btn"><i></i>FOLLOW US</div>
</section>

<footer class="footer">
  <div class="brand">
    <span class="brand__mark"></span>
    <span class="brand__name">BMRT</span>
    <span class="brand__sub">WEDDING FILMS</span>
  </div>
  <h4 style="left:441px">LINKS</h4>
  <ul style="left:443px;top:98px"><li>Home</li><li>Films</li><li>Prices</li><li>Reviews</li></ul>
  <ul style="left:531px;top:98px"><li>Options</li><li>About</li><li>Contact</li></ul>
  <h4 style="left:648px">CONTACT</h4>
  <div class="contact-row" style="left:652px;top:96px"><i><svg width="12" height="12" viewBox="0 0 24 24"><path d="M6 2l4 4-2 3a12 12 0 0 0 7 7l3-2 4 4-3 4C10 22 2 14 2 5z" fill="#fff"/></svg></i>07700 900 318</div>
  <div class="contact-row" style="left:652px;top:135px"><i><svg width="12" height="10" viewBox="0 0 24 18"><rect x="1" y="1" width="22" height="16" fill="#fff"/><polyline points="1,1 12,10 23,1" fill="none" stroke="#2b2b2b" stroke-width="2"/></svg></i><a>films@bmrtfilms.com</a></div>
  <h4 style="left:906px">FOLLOW US</h4>
  <div class="contact-row" style="left:906px;top:96px"><i></i>Circlebook</div>
  <div class="contact-row" style="left:906px;top:135px"><i></i>Snapgrid</div>
  <div class="contact-row" style="left:906px;top:174px"><i></i>Reeltube</div>
  <div class="footer__rule"></div>
  <p class="footer__copy">Copyright 2020 All Rights Reserved</p>
  <div class="footer__badge"></div>
</footer>

</body>
</html>
```